Computer consultant business card

Bexil Software is a newly started computer consulting company. It's a small one-man company that provides mostly Vornix applications but also websites in collaboration with designers. I'm running this company on the side of full time university studies.

I want the final design to be clean and memorable. Be creative! :)

Some inspiration:
http://www.pixelmarta.com/design/48317
http://www.pixelmarta.com/design/2739164/business-card-design-by-frostlynk
http://www.pixelmarta.com/design/604281/business-card-design-by-koralind-vestrabanu

See attachment for my company logo.
Updates

I would like to thank everyone for submitting! I'll need a couple of days to review and ultimately select a design.

Target Market(s)

Non-technical entrepreneurs and small companies.

Industry/Entity Type

University

Requirements
Must have
• My company logo.
In any way, both colors from my logo.
First- and last name, e-mail and phone number.
Double-sided design.
Nice to have
• Something creative with the symbol in my logo

```html
<!DOCTYPE html>
<html lang="en">
<head>
<meta charset="utf-8">
<title>Quorvy Software – Business Card</title>
<link href="https://fonts.googleapis.com/css2?family=Exo+2:wght@400;600;700&display=swap" rel="stylesheet">
<style>
  :root {
    --page-bg: #e9e9e9;
    --metal-light: #f1f1f1;
    --metal-mid: #d6d6d6;
    --metal-dark: #bdbdbd;
    --ink: #333333;
    --brand-blue: #1f7ef5;
    --card-shadow: rgba(0, 0, 0, 0.25);
  }
  * { margin: 0; padding: 0; box-sizing: border-box; }
  html, body {
    width: 1200px;
    height: 785px;
    overflow: hidden;
    background: var(--page-bg);
    font-family: "Exo 2", sans-serif;
    color: var(--ink);
  }
  .stage {
    position: relative;
    width: 1200px;
    height: 785px;
  }
  .card {
    position: absolute;
    top: 238px;
    width: 540px;
    height: 309px;
    border-radius: 22px;
    overflow: hidden;
    background: linear-gradient(115deg, var(--metal-mid) 0%, var(--metal-light) 35%, var(--metal-mid) 60%, var(--metal-light) 80%, var(--metal-dark) 100%);
    box-shadow: 0 8px 20px var(--card-shadow);
  }
  .card--front { left: 45px; }
  .card--back { left: 615px; }

  /* Front */
  .brand {
    position: absolute;
    left: 44px;
    top: 38px;
    display: flex;
    align-items: center;
    gap: 16px;
  }
  .brand__dot {
    width: 70px;
    height: 70px;
    border-radius: 50%;
    background: var(--brand-blue);
    flex: none;
  }
  .brand__name {
    font-weight: 600;
    font-size: 72px;
    line-height: 1;
    color: var(--ink);
    letter-spacing: 1px;
    padding-bottom: 12px;
  }
  .holder {
    position: absolute;
    left: 44px;
    top: 150px;
    font-size: 20px;
    color: var(--ink);
  }
  .holder__first {
    font-weight: 700;
    color: var(--brand-blue);
  }
  .contact {
    position: absolute;
    left: 44px;
    top: 194px;
    list-style: none;
    font-size: 14px;
    line-height: 1;
  }
  .contact__item {
    display: flex;
    align-items: center;
    gap: 9px;
    margin-bottom: 13px;
  }
  .contact__icon { width: 12px; height: 12px; flex: none; }
  .band {
    position: absolute;
    left: 0;
    top: 240px;
    width: 540px;
    height: 69px;
  }
  .band-mark {
    position: absolute;
    left: 418px;
    top: 196px;
    width: 56px;
    height: 56px;
    border-radius: 50%;
    background: var(--brand-blue);
  }

  /* Back */
  .back-name {
    position: absolute;
    inset: 0;
    display: flex;
    align-items: center;
    justify-content: center;
    font-weight: 600;
    font-size: 120px;
    line-height: 1;
    color: var(--ink);
    letter-spacing: 2px;
    padding-bottom: 20px;
  }
</style>
</head>
<body>
<main class="stage">

  <section class="card card--front" aria-label="Business card front">
    <div class="brand">
      <span class="brand__dot" aria-hidden="true"></span>
      <span class="brand__name">quorvy</span>
    </div>

    <p class="holder"><span class="holder__first">First Name,</span> Last Name</p>

    <ul class="contact">
      <li class="contact__item">
        <svg class="contact__icon" viewBox="0 0 12 12" aria-hidden="true">
          <circle cx="6" cy="6" r="5.3" fill="none" stroke="var(--brand-blue)" stroke-width="1.2"/>
          <path d="M4.2 3.3 L5.2 3.3 L5.5 4.6 L4.9 5.1 Q5.6 6.6 6.9 7.1 L7.4 6.5 L8.7 6.8 L8.7 7.8 Q6 8.4 3.9 5.6 Q3.6 4.3 4.2 3.3 Z" fill="var(--brand-blue)"/>
        </svg>
        <span>0961 284730</span>
      </li>
      <li class="contact__item">
        <svg class="contact__icon" viewBox="0 0 12 12" aria-hidden="true">
          <rect x="1" y="3" width="10" height="7" rx="1" fill="var(--brand-blue)"/>
          <path d="M1.5 3.5 L6 7 L10.5 3.5" fill="none" stroke="#ffffff" stroke-width="1"/>
        </svg>
        <span>info@quorvy.com</span>
      </li>
    </ul>

    <svg class="band" viewBox="0 0 540 69" aria-hidden="true">
      <path d="M0 36 H400 Q410 36 414 26 L418 16 H540 V69 H0 Z" fill="var(--brand-blue)"/>
      <rect x="0" y="40" width="540" height="3" fill="var(--metal-light)" opacity="0.7"/>
    </svg>
    <span class="band-mark" aria-hidden="true"></span>
  </section>

  <section class="card card--back" aria-label="Business card back">
    <span class="back-name">quorvy</span>
  </section>

</main>
</body>
</html>
```